Venture 482 - Lumora Book Cover

I am looking for a Lumora book cover for my book about "Venture 482".
The Book is Titled:
Venture 482 Ascended
Shaping Outcomes: Paths To Unlocking Cosmic Truths
Author is Dorian Pell
Here is a book description that may help you understand more about it:
Inspired by the genius of Edwin Marlowe, this comprehensive guide delves into the ancient wisdom and cutting-edge science behind the 482 method, a powerful tool for manifesting your desires. Whether you're seeking personal growth, financial success, or spiritual enlightenment, this book provides advanced techniques and methods to transform your dreams into reality.
Any questions please ask.
Thanks
Owen

```html
<!DOCTYPE html>
<html lang="en">
<head>
<meta charset="utf-8">
<title>Venture 482 Ascended — Dorian Pell</title>
<link rel="stylesheet" href="https://fonts.googleapis.com/css2?family=Cinzel:wght@400&family=Cormorant+Garamond:ital,wght@0,400;0,500;1,400&family=Tinos&display=swap">
<style>
  :root {
    --ink-pale: #f6e3d6;
    --ink-light: #fbeee6;
    --space-deep: #0d1320;
    --space-navy: #1b2738;
    --glow-amber: #e39a3a;
    --glow-gold: #f6c766;
    --glow-ember: #7a3c18;
    --shadow-dark: rgba(10, 8, 6, 0.85);
  }
  * { margin: 0; padding: 0; box-sizing: border-box; }
  html, body {
    width: 805px; height: 1200px; overflow: hidden;
    background: var(--space-deep);
  }
  .cover {
    position: relative; width: 805px; height: 1200px; overflow: hidden;
    color: var(--ink-pale);
  }
  .cover-art {
    position: absolute; inset: 0;
    background:
      radial-gradient(ellipse 160px 420px at 50% 52%, rgba(246,199,102,0.55), transparent 70%),
      radial-gradient(ellipse 260px 180px at 42% 18%, rgba(227,154,58,0.5), transparent 70%),
      radial-gradient(ellipse 240px 200px at 85% 80%, rgba(246,180,80,0.55), transparent 70%),
      radial-gradient(ellipse 220px 160px at 10% 45%, rgba(227,140,50,0.4), transparent 70%),
      radial-gradient(ellipse 200px 160px at 88% 30%, rgba(200,120,50,0.35), transparent 70%),
      radial-gradient(ellipse 420px 520px at 50% 50%, rgba(122,60,24,0.55), transparent 75%),
      linear-gradient(160deg, var(--space-navy), var(--space-deep) 60%, #1a1410);
  }
  .author, .title-word, .title-number, .edition, .subtitle-lead, .subtitle-rest {
    position: absolute; left: 0; width: 100%; text-align: center;
  }
  .author {
    top: 72px;
    font-family: "Cinzel", "Cormorant Garamond", serif;
    font-size: 50px; letter-spacing: 0.3em; padding-left: 0.3em;
    color: var(--ink-pale);
  }
  .title-word {
    top: 360px;
    font-family: "Cinzel", serif;
    font-size: 112px; line-height: 1; letter-spacing: -0.01em;
    color: var(--ink-light);
  }
  .title-number {
    top: 500px; height: 380px;
    font-family: "Cormorant Garamond", serif;
    font-weight: 500; color: var(--ink-light);
  }
  .title-number .digit {
    position: absolute; font-size: 340px; line-height: 1;
  }
  .digit-first { left: 206px; top: -20px; }
  .digit-second { left: 376px; top: 50px; }
  .digit-third { left: 528px; top: -20px; }
  .edition {
    top: 885px;
    font-family: "Cinzel", serif;
    font-size: 60px; letter-spacing: 0.42em; padding-left: 0.42em;
    color: var(--ink-light);
    text-shadow: 3px 3px 3px var(--shadow-dark);
  }
  .subtitle-lead {
    top: 993px;
    font-family: "Tinos", "Times New Roman", serif;
    font-size: 26px; color: var(--ink-light);
  }
  .subtitle-rest {
    top: 1040px;
    font-family: "Tinos", "Times New Roman", serif;
    font-size: 22px; line-height: 1.5; color: var(--ink-light);
  }
</style>
</head>
<body>
  <main class="cover">
    <div class="cover-art" role="img" aria-label="Glowing golden human figure stepping forward amid swirling cosmic energy streams and sparks on a dark blue starfield"></div>
    <p class="author">DORIAN PELL</p>
    <h1>
      <span class="title-word">Venture</span>
      <span class="title-number">
        <span class="digit digit-first">4</span>
        <span class="digit digit-second">8</span>
        <span class="digit digit-third">2</span>
      </span>
    </h1>
    <p class="edition">ASCENDED</p>
    <p class="subtitle-lead">SHAPING OUTCOMES:</p>
    <p class="subtitle-rest">Paths to unlocking<br>cosmic truths</p>
  </main>
</body>
</html>
```